Gobal construction supply company needs new business card design

I need a business card design for my global supply company using an existing logo. i will be looking to print these on rounded corner cards with the black background version of my logo on the back. on the front white background, my logo again and my simple details.

```html
<!DOCTYPE html>
<html lang="en">
<head>
<meta charset="utf-8">
<title>Meridian Build Supply — Business Cards</title>
<link rel="stylesheet" href="https://fonts.googleapis.com/css2?family=Montserrat:wght@500;600;700&family=Work+Sans:wght@400;500&display=swap">
<style>
  :root {
    --stage: #1f2224;
    --card-dark: #231f20;
    --card-light: #ffffff;
    --brand-red: #d7222a;
    --ink: #231f20;
    --paper-text: #ffffff;
    --map-tone: #3a3637;
  }
  * { margin: 0; padding: 0; box-sizing: border-box; }
  html, body {
    width: 1200px; height: 738px; overflow: hidden;
    background: var(--stage);
  }
  .stage {
    position: relative; width: 1200px; height: 738px;
  }
  .card {
    position: absolute; width: 540px; height: 309px;
    border-radius: 14px; overflow: hidden;
  }
  .card--back { left: 40px; top: 214px; background: var(--card-dark); }
  .card--front { left: 620px; top: 214px; background: var(--card-light); }

  .world-map {
    position: absolute; left: 40px; top: 30px; width: 460px; height: 250px;
    border-radius: 40px;
    background: radial-gradient(ellipse at center, var(--map-tone) 0%, rgba(58,54,55,0.35) 55%, rgba(35,31,32,0) 80%);
  }
  .brand {
    position: absolute; display: flex; align-items: center; gap: 10px;
    font-family: "Montserrat", sans-serif; font-weight: 700;
    letter-spacing: 0.5px; white-space: nowrap;
  }
  .brand__dot {
    width: 14px; height: 14px; border-radius: 50%; background: var(--brand-red);
  }
  .card--back .brand {
    left: 0; right: 0; top: 138px; justify-content: center;
    font-size: 25px; color: var(--paper-text);
  }
  .card--front .brand {
    left: 36px; top: 112px; font-size: 21px; color: var(--ink);
  }

  .wave { position: absolute; inset: 0; width: 540px; height: 309px; }

  .person {
    position: absolute; right: 26px; top: 20px; text-align: right;
    font-family: "Montserrat", sans-serif;
  }
  .person__name { font-size: 18px; font-weight: 600; color: var(--brand-red); letter-spacing: 0.3px; }
  .person__role { font-family: "Work Sans", sans-serif; font-size: 10px; color: var(--ink); margin-top: 1px; }

  .contact {
    position: absolute; right: 22px; top: 204px; text-align: right;
    font-family: "Work Sans", sans-serif; font-size: 12.5px; line-height: 16px;
    color: var(--paper-text); list-style: none; letter-spacing: 0.4px;
  }
  .contact li { display: flex; justify-content: flex-end; align-items: center; gap: 7px; }
  .contact__icon { width: 9px; height: 9px; flex: none; }
  .contact__spacer { width: 9px; flex: none; }
</style>
</head>
<body>
<main class="stage">

  <section class="card card--back" aria-label="Card back">
    <div class="world-map" role="img" aria-label="Faint dotted world map behind the company name"></div>
    <div class="brand"><span>MERIDIAN BUILD SUPPLY</span><span class="brand__dot"></span></div>
  </section>

  <section class="card card--front" aria-label="Card front">
    <svg class="wave" viewBox="0 0 540 309" aria-hidden="true">
      <path d="M0,228 C160,270 300,222 360,152 C410,94 480,72 540,64 L540,309 L0,309 Z" fill="var(--brand-red)"/>
      <path d="M60,250 C200,266 300,234 360,166 C410,108 480,86 540,78" fill="none" stroke="#ffffff" stroke-width="3"/>
      <path d="M0,258 C160,300 300,250 360,180 C410,120 480,96 540,88 L540,309 L0,309 Z" fill="var(--card-dark)"/>
    </svg>

    <div class="person">
      <div class="person__name">DANIEL HART</div>
      <div class="person__role">Director</div>
    </div>

    <div class="brand"><span>MERIDIAN BUILD SUPPLY</span><span class="brand__dot"></span></div>

    <ul class="contact">
      <li><span>48 Harbour Road Box</span><span class="contact__spacer"></span></li>
      <li><span>920, Lakeview, AB</span><span class="contact__spacer"></span></li>
      <li><span>403-555-0182</span>
        <svg class="contact__icon" viewBox="0 0 10 10" aria-hidden="true"><path d="M2,1 L4,1 L4.6,3.2 L3.5,4 C4,5.2 4.8,6 6,6.5 L6.8,5.4 L9,6 L9,8 C9,8.6 8.6,9 8,9 C4.5,9 1,5.5 1,2 C1,1.4 1.4,1 2,1 Z" fill="var(--brand-red)"/></svg>
      </li>
      <li><span>info@meridianbuild.com</span>
        <svg class="contact__icon" viewBox="0 0 10 10" aria-hidden="true"><rect x="1" y="2.2" width="8" height="5.6" fill="none" stroke="var(--brand-red)" stroke-width="1"/><path d="M1,2.4 L5,5.4 L9,2.4" fill="none" stroke="var(--brand-red)" stroke-width="1"/></svg>
      </li>
      <li><span>www.meridianbuild.com</span>
        <svg class="contact__icon" viewBox="0 0 10 10" aria-hidden="true"><circle cx="5" cy="5" r="4" fill="none" stroke="var(--brand-red)" stroke-width="1"/><ellipse cx="5" cy="5" rx="1.8" ry="4" fill="none" stroke="var(--brand-red)" stroke-width="0.8"/><path d="M1,5 L9,5" stroke="var(--brand-red)" stroke-width="0.8"/></svg>
      </li>
    </ul>
  </section>

</main>
</body>
</html>
```